Web Design Project!!

This is the clients current site: http://marlowkitchenworks.com/
I want this new design to be AMAZING! I think the current site looks fine, but the client is wanting a lot of new features added to the site so will need a new design. I need a home page design and a simple internal page also. Social media is one of the most important features of the site. Contact me with any questions. I am really just letting you all flow with this project. If you look at the clients show office location, you will see it looks amazing!
I have attached the proposal of features that are going to be needed in the site and page names.
Media

```html
<!DOCTYPE html>
<html lang="en">
<head>
<meta charset="utf-8">
<title>Marlow Kitchenworks – Home</title>
<link href="https://fonts.googleapis.com/css2?family=Arimo:wght@400;700&family=Oswald:wght@400;500&display=swap" rel="stylesheet">
<style>
:root{
  --blue-dark:#0b6d96;
  --blue-mid:#1e8fbb;
  --blue-light:#3fb0d6;
  --olive:#5b6a12;
  --green:#8cc43c;
  --text:#222;
  --muted:#666;
  --panel:#f2f2f2;
  --panel-head:#e2e2e2;
  --band:#e8e8e8;
  --beige:#ebe9e1;
  --beige-line:#cfcdc2;
  --white:#fff;
}
*{margin:0;padding:0;box-sizing:border-box}
html,body{width:787px;height:1200px;overflow:hidden}
body{position:relative;background:#fff;font-family:"Arimo",Arial,sans-serif;color:var(--text)}
.abs{position:absolute}
.header{left:0;top:0;width:787px;height:121px;background:linear-gradient(160deg,var(--blue-dark),var(--blue-mid) 55%,var(--blue-light))}
.logo{left:40px;top:33px;width:160px;height:45px;display:flex;align-items:center;gap:6px}
.logo-mark{width:14px;height:14px;background:#fff}
.logo-name{color:#fff;font-weight:700;font-size:15px;letter-spacing:.5px;line-height:1.1}
.call{right:42px;top:51px;color:#fff;font-size:16px;font-family:Georgia,serif}
.call b{font-family:"Arimo",Arial,sans-serif;font-weight:400;font-size:17px}
.nav{left:0;top:121px;width:787px;height:42px;background:#fff;border-bottom:4px solid #d8d8d8}
.nav a{position:absolute;top:16px;font-size:10.5px;color:var(--text);text-decoration:none;white-space:nowrap}
.nav a.active{color:var(--blue-mid)}
.nav-pointer{left:37px;top:157px;width:0;height:0;border:5px solid transparent;border-bottom-color:#d8d8d8}
.slider-band{left:0;top:167px;width:787px;height:288px;background:var(--band);border-bottom:1px solid #d0d0d0}
.card{background:var(--beige);border:1px solid var(--beige-line);border-radius:4px}
.showroom-art{left:11px;top:13px;width:62px;height:76px;background:linear-gradient(#c7d19b,#8b9a4c);border-radius:3px}
.showroom-text{left:83px;top:18px;width:148px;font-size:10px;line-height:15px;color:#333}
.learn{right:14px;top:84px;font-size:10px;color:var(--olive);text-decoration:underline}
.news-title{left:9px;top:14px;font-size:11px;font-weight:700;color:var(--olive)}
.news-input{left:9px;top:37px;width:147px;height:21px;background:#a9a7a0;border-radius:4px;border:1px solid #8e8c85}
.news-btn{left:164px;top:38px;width:55px;height:20px;background:linear-gradient(#b3de6a,var(--green));border-radius:4px;font-size:10px;font-weight:700;color:#35500a;text-align:center;line-height:20px}
.news-check{left:38px;top:74px;width:8px;height:8px;border:1px solid #999;background:#fff}
.news-note{left:51px;top:72px;width:180px;font-size:8px;line-height:12px;color:#666}
.slide{left:286px;top:182px;width:472px;height:238px;background:#fff;box-shadow:0 2px 6px rgba(0,0,0,.25)}
.slide-img{left:12px;top:13px;width:449px;height:213px;background:linear-gradient(90deg,#b9bcbd,#8d8f8f 30%,#3a2a22 55%,#d8d6d2 80%,#4a3226)}
.ribbon{left:-4px;top:-4px;width:80px;height:80px;overflow:hidden}
.ribbon span{position:absolute;left:-22px;top:26px;width:120px;transform:rotate(-45deg);background:var(--green);color:#fff;font-size:9px;font-weight:700;text-align:center;line-height:16px}
.s-arrow{top:285px;width:18px;height:32px;background:#3a3a3a;color:#fff;font-size:12px;line-height:32px;text-align:center}
.dot{top:432px;width:8px;height:8px;border-radius:50%;background:#999}
.sec-head{height:24px;background:var(--panel-head);font-size:13px;font-weight:700;color:var(--olive);padding:4px 7px}
.body-text{font-size:9.5px;line-height:15px;color:#555;text-align:justify}
.panel{background:var(--panel)}
.ev{position:absolute;left:0;width:337px;height:70px}
.cal{left:25px;top:11px;width:32px;height:36px;border:2px solid #333;border-top:7px solid #2a6bb8;border-radius:3px;background:#fff;font-size:13px;font-weight:700;text-align:center;line-height:25px}
.ev-title{left:78px;top:10px;font-size:10px;font-weight:700}
.ev-desc{left:78px;top:29px;width:250px;font-size:9.5px;line-height:14px;color:var(--muted)}
.more{right:9px;font-size:10px;font-weight:700;color:#555}
.video{left:564px;top:496px;width:192px;height:128px;background:linear-gradient(135deg,#dbe6f2,#6b8ad6 55%,#3f57b8);border:1px solid #bbb}
.video-bar{left:0;bottom:0;width:190px;height:10px;background:#ddd}
.fb{left:377px;top:648px;width:381px;height:109px;border:1px solid #bfc8dd;background:#fff}
.fb-top{left:0;top:0;width:379px;height:44px;background:#edeff4}
.fb-pic{left:4px;top:4px;width:30px;height:32px;background:#d9b24a}
.fb-name{left:40px;top:7px;font-size:9px;color:#3b5998;font-weight:700}
.fb-name span{font-weight:400;font-size:7px}
.fb-like{left:40px;top:20px;width:30px;height:13px;background:#5f78ab;color:#fff;font-size:7px;text-align:center;line-height:13px}
.fb-you{left:75px;top:23px;font-size:7px;color:#555}
.fb-label{left:232px;top:12px;font-family:"Oswald",sans-serif;font-size:12px;color:#4a5fa0}
.fb-count{left:6px;top:48px;font-size:7px;color:#333}
.av{top:58px;width:30px;height:32px;background:linear-gradient(#c9b8a6,#7d6c60)}
.av-name{top:92px;width:30px;font-size:6px;color:#666;text-align:center}
.tw{left:377px;top:766px;width:381px;height:127px;background:#cfe8f2;border-radius:6px}
.tw-label{left:9px;top:42px;width:60px;font-size:8px;color:#2a8bb8;text-align:center}
.tw-label b{display:block;font-size:13px}
.tw-box{left:77px;top:6px;width:294px;height:113px;background:#fff;border:1px solid #aaa}
.tab{top:2px;height:11px;font-size:6.5px;color:#444;border:1px solid #ccc;background:#eee;text-align:center;line-height:10px}
.tweet{left:4px;width:280px;height:28px;font-size:7.5px;line-height:10px;color:#222}
.tweet i{position:absolute;left:0;top:1px;width:22px;height:22px;background:#b8b3ad}
.tweet p{margin-left:28px}
.tweet b{color:#2a5aa0}
.tweet small{font-size:6px;color:#2a8bb8}
.lower{left:0;top:905px;width:787px;height:228px;background:#e6e6e6}
.wide-head{left:23px;width:739px;height:24px;background:#d3d3d3;font-size:13px;font-weight:700;color:var(--olive);padding:4px 10px}
.thumb{top:947px;width:111px;height:57px;border:2px solid #aaa;border-radius:3px;background:linear-gradient(135deg,#efe9df,#8d7a62 60%,#3a3028)}
.p-arrow{top:962px;font-size:22px;color:#888}
.partner{top:1078px;font-size:15px;font-weight:700;white-space:nowrap}
.footer{left:0;top:1133px;width:787px;height:67px;background:linear-gradient(var(--blue-mid),var(--blue-dark))}
.foot-links a{position:absolute;top:16px;color:#fff;font-size:9px;text-decoration:none;white-space:nowrap}
.foot-small{top:46px;color:#fff;font-size:9px;white-space:nowrap}
.card-chip{top:43px;width:22px;height:14px;background:#fff;border-radius:2px;font-size:5px;font-weight:700;color:#1a4d7a;text-align:center;line-height:14px}
.social{top:38px;width:24px;height:24px;border-radius:50%;background:#fff}
</style>
</head>
<body>

<header class="abs header">
  <div class="abs logo"><span class="logo-mark"></span><span class="logo-name">MARLOW<br>KITCHENWORKS</span></div>
  <div class="abs call">Call Us : <b>123 456 7890</b></div>
</header>

<nav class="abs nav">
  <a class="active" style="left:29px">Home</a>
  <a style="left:79px">Company</a>
  <a style="left:145px">Showroom</a>
  <a style="left:217px">Testimonials</a>
  <a style="left:296px">Upcoming events</a>
  <a style="left:398px">Blog</a>
  <a style="left:441px">Brands</a>
  <a style="left:497px">Service request</a>
  <a style="left:590px">Directions</a>
  <a style="left:658px">Contact us</a>
  <a style="left:730px">Media</a>
</nav>
<div class="abs nav-pointer"></div>

<section class="abs slider-band"></section>

<div class="abs card" style="left:13px;top:181px;width:240px;height:113px">
  <div class="abs showroom-art" role="img" aria-label="Open Hearth showroom emblem"></div>
  <p class="abs showroom-text">Come visit our brand new location and view the new Open Hearth showroom. It's an experience you won't forget.</p>
  <a class="abs learn">Learn more...</a>
</div>

<div class="abs card" style="left:13px;top:309px;width:240px;height:112px">
  <div class="abs news-title">NEWS LETTER</div>
  <div class="abs news-input"></div>
  <div class="abs news-btn">Subscribe</div>
  <div class="abs news-check"></div>
  <p class="abs news-note">Ferrin pages are also reproduced in their exact original form, accompanied by English</p>
</div>

<div class="abs slide">
  <div class="abs slide-img" role="img" aria-label="Modern kitchen with dark wood island and grey walls"></div>
  <div class="abs ribbon"><span>WHAT'S HOT!</span></div>
</div>
<div class="abs s-arrow" style="left:268px;border-radius:16px 0 0 16px">&#8249;</div>
<div class="abs s-arrow" style="left:758px;border-radius:0 16px 16px 0">&#8250;</div>
<div class="abs dot" style="left:495px"></div>
<div class="abs dot" style="left:507px"></div>
<div class="abs dot" style="left:519px;background:var(--green)"></div>
<div class="abs dot" style="left:531px"></div>
<div class="abs dot" style="left:543px"></div>

<div class="abs sec-head" style="left:23px;top:467px;width:337px">Welcome To Our Site</div>
<p class="abs body-text" style="left:24px;top:498px;width:333px">The standard chunk of Lorem Ipsum used since the 1500s is reproduced below for those interested. Sections 1.10.32 and 1.10.33 from "Notes on Lasting Good Works" by Aldo Ferrin are also reproduced in their exact original form, accompanied by English versions from the 1914 translation by J. Penlow.</p>

<div class="abs sec-head" style="left:377px;top:467px;width:383px">Latest Video</div>
<p class="abs body-text" style="left:384px;top:497px;width:162px;font-size:9px;line-height:14px;color:#777">The standard chunk of Lorem Ipsum used since the 1500s is reproduced below for those interested. Sections 1.10.32 and 1.10.33 from "Notes on Lasting Good Works" by Aldo Ferrin.</p>
<div class="abs video" role="img" aria-label="Video still of a blue modern kitchen">
  <div class="abs video-bar"><svg width="190" height="10"><polygon points="5,2 5,8 10,5" fill="#444"/><rect x="16" y="4" width="120" height="2" fill="#aaa"/><rect x="16" y="4" width="48" height="2" fill="#d02020"/><text x="142" y="8" font-size="5" fill="#444">1:47 / 5:00</text><rect x="172" y="3" width="14" height="4" fill="#888"/></svg></div>
</div>

<div class="abs panel" style="left:23px;top:584px;width:337px;height:174px">
  <div class="abs sec-head" style="left:0;top:0;width:337px;height:22px;padding-top:3px">Events<span style="position:absolute;right:14px;color:#333;font-size:12px">&#8249; &#8250;</span></div>
  <div class="ev" style="top:22px">
    <div class="abs cal">14</div>
    <div class="abs ev-title">Lorem Ipsum Contantry Dummy Text</div>
    <p class="abs ev-desc">Sections 1.10.32 and 1.10.33 from "Notes on Lasting Good Works" by Aldo Ferrin</p>
    <div class="abs more" style="top:60px">View more</div>
  </div>
  <div class="abs" style="left:2px;top:99px;width:333px;height:1px;background:#d6d6d6"></div>
  <div class="ev" style="top:93px">
    <div class="abs cal">14</div>
    <div class="abs ev-title">Lorem Ipsum Contantry Dummy Text</div>
    <p class="abs ev-desc">Sections 1.10.32 and 1.10.33 from "Notes on Lasting Good Works" by Aldo Ferrin</p>
    <div class="abs more" style="top:60px">View more</div>
  </div>
</div>

<div class="abs panel" style="left:23px;top:768px;width:337px;height:132px">
  <div class="abs sec-head" style="left:0;top:0;width:337px;height:22px;padding-top:3px">Our Blog</div>
  <div class="abs" style="left:10px;top:34px;width:131px;height:78px;border:3px solid #fff;border-radius:6px;box-shadow:0 1px 4px rgba(0,0,0,.4);background:linear-gradient(120deg,#333,#8a8a8a 50%,#c9c9c9)" role="img" aria-label="Blog post photo collage"></div>
  <div class="abs ev-title" style="left:153px;top:40px">Lorem Ipsum Contantry Dummy Text</div>
  <p class="abs ev-desc body-text" style="left:153px;top:62px;width:176px;font-size:9.5px;color:var(--muted)">Sections 1.10.32 and 1.10.33 from "Notes on Lasting Good Works" by Ferrin are also reproduced.</p>
  <div class="abs more" style="top:111px">View more</div>
</div>

<div class="abs fb">
  <div class="abs fb-top"></div>
  <div class="abs fb-pic" role="img" aria-label="Kettle Corner page picture"></div>
  <div class="abs fb-name">Kettle Corner <span>on FriendWall</span></div>
  <div class="abs fb-like">Like</div>
  <div class="abs fb-you">You like this.</div>
  <div class="abs fb-label">FRIENDWALL LIKE BOX</div>
  <div class="abs fb-count">64 people like Kettle Corner</div>
  <div class="abs av" style="left:6px" role="img" aria-label="Fan photo"></div><div class="abs av-name" style="left:6px">Ravi</div>
  <div class="abs av" style="left:41px" role="img" aria-label="Fan photo"></div><div class="abs av-name" style="left:41px">Nora</div>
  <div class="abs av" style="left:76px" role="img" aria-label="Fan photo"></div><div class="abs av-name" style="left:76px">Colin</div>
  <div class="abs av" style="left:111px" role="img" aria-label="Fan photo"></div><div class="abs av-name" style="left:111px">Elise</div>
  <div class="abs av" style="left:146px" role="img" aria-label="Fan photo"></div><div class="abs av-name" style="left:146px">Tarun</div>
  <div class="abs av" style="left:181px" role="img" aria-label="Fan photo"></div><div class="abs av-name" style="left:181px">Milo</div>
  <div class="abs av" style="left:216px" role="img" aria-label="Fan photo"></div><div class="abs av-name" style="left:216px">Amar</div>
  <div class="abs av" style="left:251px" role="img" aria-label="Fan photo"></div><div class="abs av-name" style="left:251px">Irene</div>
  <div class="abs av" style="left:286px" role="img" aria-label="Fan photo"></div><div class="abs av-name" style="left:286px">Mira</div>
  <div class="abs av" style="left:321px;background:linear-gradient(#f6c042,#e86f1d)" role="img" aria-label="Fan photo"></div><div class="abs av-name" style="left:321px">Oren</div>
</div>

<div class="abs tw">
  <div class="abs" style="left:18px;top:20px;width:30px;height:20px;border-radius:50%;background:#fff"></div>
  <div class="abs tw-label">FOLLOW US ON<b>Chirper</b></div>
  <div class="abs tw-box">
    <div class="abs tab" style="left:82px;width:40px">Archive</div>
    <div class="abs tab" style="left:124px;width:40px">Replies</div>
    <div class="abs tab" style="left:166px;width:40px;background:#fff">Recent</div>
    <div class="abs tweet" style="top:17px"><i></i><p><b>danmercer</b> @Orbitlab more or less. should have translated as "Just to say hello and I hope that you can read this. Good Luck!" <small>less than a minute ago from web</small></p></div>
    <div class="abs tweet" style="top:50px"><i></i><p><b>rayKD</b> Grabbing a quick lunch after critical path analysis but before resource levelling <small>4 minutes ago from web</small></p></div>
    <div class="abs tweet" style="top:82px"><i></i><p><b>rayKD</b> Grabbing a quick lunch after critical path analysis but before resource levelling <small>4 minutes ago from web</small></p></div>
  </div>
</div>

<section class="abs lower"></section>
<div class="abs wide-head" style="top:913px">Photo</div>
<div class="abs p-arrow" style="left:36px">&#8249;</div>
<div class="abs thumb" style="left:61px" role="img" aria-label="Kitchen photo"></div>
<div class="abs thumb" style="left:203px" role="img" aria-label="Kitchen photo"></div>
<div class="abs thumb" style="left:344px" role="img" aria-label="Kitchen photo"></div>
<div class="abs thumb" style="left:478px" role="img" aria-label="Kitchen photo"></div>
<div class="abs thumb" style="left:613px;background:linear-gradient(135deg,#f3f3f1,#c9c7c2 60%,#55524d)" role="img" aria-label="Kitchen photo"></div>
<div class="abs p-arrow" style="left:737px">&#8250;</div>

<div class="abs wide-head" style="top:1025px">Our Partners</div>
<div class="abs partner" style="left:45px;color:#333">Hearthline</div>
<div class="abs partner" style="left:146px;color:#3a8a2a">Stir&amp;Serve</div>
<div class="abs partner" style="left:240px;color:#c0282d">Pan Pantry</div>
<div class="abs partner" style="left:336px;color:#8a2a1a">Oakroom</div>
<div class="abs partner" style="left:430px;color:#d8641e">Brightbench</div>
<div class="abs partner" style="left:578px;color:#2a6a7a">Ladle Co</div>
<div class="abs partner" style="left:654px;color:#333">Tessa Interiors</div>

<footer class="abs footer">
  <div class="foot-links">
    <a style="left:73px">Home</a><a style="left:113px">Company</a><a style="left:167px">Showroom</a><a style="left:225px">Testimonials</a><a style="left:290px">Upcoming events</a><a style="left:372px">Blog</a><a style="left:406px">Brands</a><a style="left:452px">Service request</a><a style="left:529px">Directions</a><a style="left:584px">Contact us</a><a style="left:642px">Media</a><a style="left:682px">Sitemap</a>
  </div>
  <div class="abs foot-small" style="left:42px">Copyright @ 2011 www.marlowkitchenworks.com All rights reserved</div>
  <div class="abs foot-small" style="left:330px">Payments :</div>
  <div class="abs card-chip" style="left:377px">Paxa</div>
  <div class="abs card-chip" style="left:402px">Vella</div>
  <div class="abs card-chip" style="left:427px">Amtro</div>
  <div class="abs card-chip" style="left:452px">Disko</div>
  <div class="abs foot-small" style="left:519px">Connect with us :</div>
  <div class="abs social" style="left:593px" aria-label="FriendWall"></div>
  <div class="abs social" style="left:625px" aria-label="Chirper"></div>
  <div class="abs social" style="left:657px" aria-label="Blogspace"></div>
  <div class="abs social" style="left:689px" aria-label="WorkLink"></div>
  <div class="abs social" style="left:721px" aria-label="Searcha"></div>
</footer>

</body>
</html>
```